Tallowood building company Business card design

I need a business card design for my company. I have a logo but dont have business cards with our logo..

www.tallowoodbuildingco.com.au

The logo is on the website

I need the same details as this design I have attached. we have changed the logo and colours. just like the website

Building

```html
<!DOCTYPE html>
<html lang="en">
<head>
<meta charset="utf-8">
<title>Tallowood Building – Business Card</title>
<link rel="stylesheet" href="https://fonts.googleapis.com/css2?family=Cinzel:wght@400;600&family=Lato:wght@400&display=swap">
<style>
  :root {
    --backdrop: #3a3a3a;
    --card-white: #ffffff;
    --card-black: #050505;
    --brand-blue: #0f86c6;
    --band-grey: #b9bbbe;
    --ink-dark: #1d1d1d;
    --ink-light: #ffffff;
  }
  * { box-sizing: border-box; margin: 0; padding: 0; }
  html, body { width: 1200px; height: 800px; overflow: hidden; }
  body {
    background: var(--backdrop);
    display: flex; align-items: center; justify-content: center; gap: 40px;
    font-family: "Lato", Arial, sans-serif;
  }
  .card {
    position: relative; width: 560px; height: 320px; overflow: hidden;
    box-shadow: 0 6px 18px rgba(0,0,0,.35);
  }

  /* Front */
  .card--front { background: var(--card-white); color: var(--ink-dark); }
  .front-band { position: absolute; inset: 0; }
  .holder { position: absolute; top: 20px; right: 30px; text-align: right; }
  .holder__name { font-family: "Cinzel", Georgia, serif; font-size: 19px; letter-spacing: .5px; color: var(--ink-dark); }
  .holder__role { font-size: 14px; color: var(--brand-blue); margin-top: 2px; }

  .wordmark { display: flex; align-items: center; gap: 10px; }
  .wordmark__mark { width: 16px; height: 16px; background: var(--brand-blue); flex: none; }
  .wordmark__name {
    font-family: "Cinzel", Georgia, serif; font-weight: 600; letter-spacing: 2px;
    color: var(--brand-blue); line-height: 1.15;
  }
  .card--front .wordmark { position: absolute; left: 34px; top: 108px; }
  .card--front .wordmark__name { font-size: 20px; }

  .contacts {
    position: absolute; left: 282px; top: 186px;
    border-left: 1px solid var(--ink-light); padding-left: 12px;
    color: var(--ink-light); font-size: 13px; line-height: 25px;
  }
  .contacts li { list-style: none; display: flex; align-items: center; gap: 8px; white-space: nowrap; }
  .contacts svg { width: 13px; height: 13px; fill: none; stroke: var(--ink-light); stroke-width: 1.4; flex: none; }

  .tagline { font-size: 14px; line-height: 1.3; }
  .card--front .tagline { position: absolute; left: 34px; bottom: 20px; color: var(--ink-light); font-size: 13px; }

  /* Back */
  .card--back { background: var(--card-black); color: var(--ink-light); }
  .rule { position: absolute; height: 1px; background: var(--ink-light); }
  .rule--top { top: 30px; right: 28px; width: 250px; }
  .rule--bottom { bottom: 30px; left: 28px; width: 250px; }
  .back-content { position: absolute; left: 60px; top: 92px; }
  .card--back .wordmark__name { font-size: 26px; }
  .card--back .tagline { margin-top: 16px; font-size: 16px; }
  .website { position: absolute; right: 28px; bottom: 58px; font-size: 14px; }
</style>
</head>
<body>

  <section class="card card--front" aria-label="Business card front">
    <svg class="front-band" viewBox="0 0 560 320" aria-hidden="true">
      <path d="M560 68 C410 92 250 184 0 230 L0 320 L560 320 Z" fill="var(--band-grey)"/>
      <path d="M560 88 C420 108 260 200 0 245 L0 320 L560 320 Z" fill="var(--brand-blue)"/>
    </svg>

    <div class="holder">
      <p class="holder__name">Marcus Hale</p>
      <p class="holder__role">Director</p>
    </div>

    <div class="wordmark">
      <span class="wordmark__mark"></span>
      <p class="wordmark__name">TALLOWOOD<br>BUILDING</p>
    </div>

    <ul class="contacts">
      <li>
        <svg viewBox="0 0 14 14"><path d="M2 5 Q7 1 12 5 L11 7 L9 6 L9 5 Q7 4 5 5 L5 6 L3 7 Z"/><rect x="3" y="8" width="8" height="4"/></svg>
        9400 1234
      </li>
      <li>
        <svg viewBox="0 0 14 14"><rect x="4" y="1.5" width="6" height="11" rx="1"/><line x1="6.3" y1="10.5" x2="7.7" y2="10.5"/></svg>
        0400123456 (Marcus)
      </li>
      <li>
        <svg viewBox="0 0 14 14"><rect x="1.5" y="3" width="11" height="8"/><path d="M1.5 3 L7 8 L12.5 3"/></svg>
        info@tallowoodbuildingco.com.au
      </li>
    </ul>

    <p class="tagline">New Homes, Addition &amp; Renovation<br>Domestic &amp; Commercial Builders</p>
  </section>

  <section class="card card--back" aria-label="Business card back">
    <span class="rule rule--top"></span>
    <div class="back-content">
      <div class="wordmark">
        <span class="wordmark__mark"></span>
        <p class="wordmark__name">TALLOWOOD<br>BUILDING</p>
      </div>
      <p class="tagline">New Homes, Addition &amp; Renovation<br>Domestic &amp; Commercial Builders</p>
    </div>
    <p class="website">www.tallowoodbuildingco.com.au</p>
    <span class="rule rule--bottom"></span>
  </section>

</body>
</html>
```